Irrigation Business needs their business cards modernised and revamped

I would like to keep my current logo, colours and revamp the format of the card.

I would like the card to be clean yet important.

Im not sure if you include texture but i would like the named logo to be indented into the card etc.

show me something alive and free something thats clinical to the point yet has a feel of achievement. i would like people to go nice card.

Target Market(s)

high end clients, corporate, sports field manger, the guys that make the decisions

Industry/Entity Type

Business

Contact Information for Business Card

nformation to be included

Dean Harlow (Director)
0487305526
dean@kolvat.biz
www.kestonfieldworks.com

instagram logo
google logo
facebook logo

Colors

Designer to choose colors to be used in the design.

Requirements
Nice to have
• indentations a really nice feel to the card good texture

```html
<!DOCTYPE html>
<html lang="en">
<head>
<meta charset="utf-8">
<title>Keston Fieldworks – Business Card</title>
<link href="https://fonts.googleapis.com/css2?family=Roboto:wght@400;500;700&display=swap" rel="stylesheet">
<style>
  :root {
    --backdrop: #2b2b2b;
    --brand-blue: #3a6aa8;
    --brand-blue-deep: #2f5d9a;
    --brand-blue-light: #4a7cb8;
    --accent-green: #2f9e5c;
    --accent-cyan: #3aa3d4;
    --card-white: #f2f2f2;
    --card-grey: #e4e4e4;
    --text-grey: #4a4a4a;
    --rule-grey: #9a9a9a;
    --white: #ffffff;
  }
  * { margin: 0; padding: 0; box-sizing: border-box; }
  html, body {
    width: 1200px; height: 1166px; overflow: hidden;
    background: var(--backdrop);
    font-family: "Roboto", Arial, sans-serif;
  }
  .canvas { position: relative; width: 1200px; height: 1166px; }

  .card {
    position: absolute; left: 233px; width: 729px; height: 417px;
    overflow: hidden;
  }

  /* Front */
  .card-front {
    top: 141px;
    background: linear-gradient(135deg, var(--card-white) 0%, var(--white) 45%, var(--card-grey) 100%);
  }
  .brand {
    position: absolute; right: 42px; top: 58px;
    display: flex; flex-direction: column; align-items: center; gap: 14px;
  }
  .brand-circle {
    width: 96px; height: 96px; border-radius: 50%;
    background: var(--accent-cyan);
  }
  .brand-name {
    font-weight: 700; font-size: 27px; letter-spacing: -0.3px;
    color: var(--brand-blue-deep); white-space: nowrap;
  }
  .person { position: absolute; left: 42px; top: 226px; }
  .person-name {
    font-weight: 500; font-size: 26px; color: var(--brand-blue-deep);
    text-transform: uppercase; letter-spacing: -0.2px;
  }
  .person-role {
    margin-top: 4px; font-size: 18px; color: var(--accent-green);
    text-transform: uppercase;
  }
  .divider {
    position: absolute; left: 42px; right: 43px; top: 290px;
    height: 1px; background: var(--rule-grey);
  }
  .contacts {
    position: absolute; left: 42px; top: 304px; list-style: none;
    font-size: 17px; color: var(--text-grey);
  }
  .contacts li { display: flex; align-items: center; height: 23px; }
  .contacts svg { width: 16px; height: 16px; margin-right: 10px; fill: var(--brand-blue-deep); }
  .card-base {
    position: absolute; left: 0; right: 0; bottom: 0; height: 20px;
    background: var(--brand-blue-deep);
    border-top: 3px solid var(--accent-cyan);
  }

  /* Back */
  .card-back {
    top: 624px;
    background: linear-gradient(160deg, var(--brand-blue) 0%, var(--brand-blue-light) 60%, var(--brand-blue) 100%);
  }
  .back-circle {
    position: absolute; left: 10px; top: 149px; transform: translateY(-50%);
    width: 400px; height: 400px; border-radius: 50%;
    border: 12px solid rgba(255,255,255,0.12);
  }
  .back-brand {
    position: absolute; left: 554px; top: 286px; transform: translateX(-50%);
    display: flex; flex-direction: column; align-items: center;
  }
  .back-name {
    font-weight: 700; font-size: 27px; color: var(--white); white-space: nowrap;
    letter-spacing: -0.3px;
  }
  .social {
    margin-top: 20px; display: flex; align-items: center; gap: 6px;
  }
  .social-line { width: 62px; height: 1px; background: rgba(255,255,255,0.45); }
  .social-dot { width: 32px; height: 32px; border-radius: 50%; background: var(--white); }
  .social-line.left { margin-right: 6px; }
  .social-line.right { margin-left: 6px; }
</style>
</head>
<body>
<main class="canvas">
  <section class="card card-front" aria-label="Business card front">
    <div class="brand">
      <div class="brand-circle"></div>
      <div class="brand-name">KESTON FIELDWORKS</div>
    </div>
    <div class="person">
      <h1 class="person-name">Dean Harlow</h1>
      <p class="person-role">Director</p>
    </div>
    <div class="divider"></div>
    <ul class="contacts">
      <li>
        <svg viewBox="0 0 24 24" aria-hidden="true"><path d="M6.6 10.8a15.1 15.1 0 0 0 6.6 6.6l2.2-2.2c.3-.3.7-.4 1-.2 1.1.4 2.3.6 3.6.6.6 0 1 .4 1 1V20c0 .6-.4 1-1 1A17 17 0 0 1 3 4c0-.6.4-1 1-1h3.5c.6 0 1 .4 1 1 0 1.3.2 2.5.6 3.6.1.3 0 .7-.2 1z"/></svg>
        0487305526
      </li>
      <li>
        <svg viewBox="0 0 24 24" aria-hidden="true"><path d="M2 5h20v14H2z M2 5l10 8 10-8" fill="none" stroke="currentColor"/><path d="M2 5h20v2l-10 7L2 7z M2 9l10 7 10-7v10H2z"/></svg>
        dean@kolvat.biz
      </li>
      <li>
        <svg viewBox="0 0 24 24" aria-hidden="true"><circle cx="12" cy="12" r="10"/></svg>
        www.kestonfieldworks.com
      </li>
    </ul>
    <div class="card-base"></div>
  </section>

  <section class="card card-back" aria-label="Business card back">
    <div class="back-circle"></div>
    <div class="back-brand">
      <div class="back-name">KESTON FIELDWORKS</div>
      <div class="social">
        <span class="social-line left"></span>
        <span class="social-dot"></span>
        <span class="social-dot"></span>
        <span class="social-dot"></span>
        <span class="social-line right"></span>
      </div>
    </div>
  </section>
</main>
</body>
</html>
```